CREATE A BUSINESS CARD FOR A BOAT CLEANING SERVICE

WE ARE STARTING A NEW BOAT CLEANING BUSINESS. WE DIVE UNDERWATER TO CLEAN BOAT HULLS, JETTIES, UNDERWATER STRUCTURES ETC. WE ARE LOOKING FOR AN UPPERMARKET MODERN LOGO AND BUSINESS CARD AS ALOT OF OUR TARGET MARKET WILL BE HIGH END. YOU HAVE TO DESIGN A BUSINESS CARD AND LOGO SEPERATELY .
THE BUSINESS CARD DIMESNION MUST BE STANDARD SIZE.
The standard dimensions of a printed business card are 3.5 x 2 inches

Target Market(s)

UNDERWATER SERVICED

Industry/Entity Type

Business

Contact Information for Business Card

HOLLAND UNDERWATER SERVICES

Font styles to use
Serif

Colors

Designer to choose colors to be used in the design.

Requirements
Must have
• HOLLAND
Nice to have
• dark
Should not have
• more than 3 colors

```html
<!DOCTYPE html>
<html lang="en">
<head>
<meta charset="utf-8">
<title>Holland Underwater Service – Business Card</title>
<link href="https://fonts.googleapis.com/css2?family=Jost:wght@400&family=Lato:wght@400&display=swap" rel="stylesheet">
<style>
  :root {
    --navy: #16508a;
    --ink: #4a4a4a;
    --paper: #ffffff;
    --backdrop: #eeeeec;
    --badge: #d9dde6;
  }
  * { margin: 0; padding: 0; box-sizing: border-box; }
  html, body { width: 1200px; height: 900px; overflow: hidden; background: var(--backdrop); }
  .canvas { position: relative; width: 1200px; height: 900px; }
  .card {
    position: absolute; top: 150px; width: 343px; height: 600px;
    text-align: center;
  }
  .card-front { left: 246px; background: var(--paper); color: var(--ink); }
  .card-back { left: 611px; background: var(--navy); color: var(--paper); }
  .line { position: absolute; left: 0; right: 0; }
  .company-name {
    font-family: "Lato", sans-serif; font-weight: 400;
    font-size: 18px; letter-spacing: 0.04em;
  }
  .card-front .company-name { color: var(--navy); }
  .card-back .company-name { color: var(--paper); }
  .person-name {
    font-family: "Jost", sans-serif; font-weight: 400;
    font-size: 22px; letter-spacing: 0.12em; color: var(--navy);
  }
  .person-role { font-family: "Lato", sans-serif; font-size: 16px; }
  .contact { font-family: "Lato", sans-serif; font-size: 14px; line-height: 19.5px; }
  .address { font-family: "Lato", sans-serif; font-size: 14px; line-height: 20px; }
  .pin { position: absolute; left: 157px; top: 402px; }
  .partner-badge { position: absolute; background: var(--badge); }
  .badge-round { left: 58px; top: 520px; width: 78px; height: 48px; border-radius: 50%; }
  .badge-wide { left: 163px; top: 522px; width: 120px; height: 38px; border-radius: 3px; }
  .back-web { font-family: "Lato", sans-serif; font-size: 15px; letter-spacing: 0.02em; }
</style>
</head>
<body>
<main class="canvas">
  <section class="card card-front" aria-label="Business card front">
    <div class="line company-name" style="top:142px">HOLLAND UNDERWATER SERVICE</div>

    <div class="line person-name" style="top:246px">DAAN VERHOEF</div>
    <div class="line person-role" style="top:276px">CEO / Founder</div>

    <div class="line contact" style="top:321px">
      555-014-2281 | 555-014-2296<br>
      info@hollandunderwaterservice.com<br>
      www.hollandunderwaterservice.com
    </div>

    <svg class="pin" width="28" height="28" viewBox="0 0 28 28" aria-hidden="true">
      <circle cx="14" cy="14" r="14" fill="var(--navy)"/>
      <path d="M14 6.5a5.2 5.2 0 0 0-5.2 5.2c0 3.9 5.2 9.3 5.2 9.3s5.2-5.4 5.2-9.3A5.2 5.2 0 0 0 14 6.5z" fill="#fff"/>
      <circle cx="14" cy="11.7" r="2" fill="var(--navy)"/>
    </svg>
    <div class="line address" style="top:440px">
      Havenkade 42 3011AB, Suite<br>
      -120, Delft, The Netherlands
    </div>

    <div class="partner-badge badge-round" role="img" aria-label="Partner badge"></div>
    <div class="partner-badge badge-wide" role="img" aria-label="Partner badge"></div>
  </section>

  <section class="card card-back" aria-label="Business card back">
    <div class="line company-name" style="top:328px">HOLLAND UNDERWATER SERVICE</div>
    <div class="line back-web" style="top:528px">www.hollandunderwaterservice.com</div>
  </section>
</main>
</body>
</html>
```